Modern Medical Optometry Website

We need mordern, Patient friendly website. Easy to navigate and enhance our advance medical technology and excellent patient care.
1. HOME PAGE
2. OUR TEAM PAGE
3. EYECARE PAGE - VISION SERVICES, EYE EXAMS, KERATOCONUS CENTER, GLAUCOMA , DIABITES, MELORIDEX EXAM, DIGITAL RETINAL, OCT.
4. MYOPIA CONTROL CLINIC
5. DRY EYE CLINIC
6. EYEWEAR
7. PATIENT CENTER - BLOG
7. CONTACT US
This is our current website www.brivaloka.com
and We want to add more content and a cleaner design like these website
http://tarnwickfolvendale.com/
https://www.qmvorlu.com/

```html
<!DOCTYPE html>
<html lang="en">
<head>
<meta charset="utf-8">
<title>Dry Eye Clinic – Lumora Optometry</title>
<link href="https://fonts.googleapis.com/css2?family=Raleway:wght@400;500;600;700&display=swap" rel="stylesheet">
<style>
:root{
  --teal:#0b8fae;
  --blue:#1665b3;
  --yellow:#fde02a;
  --footer-yellow:#fbe45c;
  --copy-yellow:#f6dc46;
  --band-grey:#eeeeee;
  --ink:#222;
  --muted:#8a8a8a;
  --white:#fff;
  --pill:#2b2b2b;
  --badge:#e8eef6;
}
*{box-sizing:border-box;margin:0;padding:0}
html,body{width:1200px;height:4354px;overflow:hidden}
body{position:relative;font-family:"Raleway",sans-serif;color:var(--ink);background:var(--white)}
.abs{position:absolute}

.topbar{left:0;top:0;width:1200px;height:51px;background:var(--teal)}
.topbar .item{top:0;height:51px;display:flex;align-items:center;gap:10px;color:var(--white);font-size:14px;padding:0 18px;border-left:1px solid rgba(255,255,255,.25)}
.topbar .social{top:0;width:52px;height:51px;border-left:1px solid rgba(255,255,255,.25);display:flex;align-items:center;justify-content:center}
.topbar .social span{width:12px;height:12px;border-radius:50%;background:var(--yellow)}

.logo{left:78px;top:20px;width:108px;height:140px;background:var(--white);box-shadow:0 2px 6px rgba(0,0,0,.08);display:flex;flex-direction:column;align-items:center;justify-content:center;gap:8px}
.logo .mark{width:44px;height:44px;background:var(--yellow)}
.logo .name{font-size:12px;font-weight:600;color:#6b6b6b;text-align:center;line-height:1.2;letter-spacing:.5px}
.nav{left:221px;top:110px;display:flex;gap:38px;font-size:16px;color:#8a8a8a;text-transform:uppercase}
.nav .active{color:var(--teal)}
.search{left:1102px;top:110px}

.title-band{left:0;top:186px;width:1200px;height:135px;background:var(--band-grey);display:flex;align-items:center;justify-content:center}
.title-band h1{font-size:36px;font-weight:700;color:var(--teal)}

.about-text{left:627px;top:378px;width:445px}
.about-text h2{font-size:22px;color:var(--teal);font-weight:700;margin-bottom:18px}
.about-text .lead{font-size:13.5px;font-weight:600;line-height:26px;margin-bottom:20px}
.about-text p{font-size:13.5px;color:var(--muted);line-height:26px;margin-bottom:26px}

.intro{width:480px}
.intro h2{font-size:30px;color:var(--teal);font-weight:700;margin-bottom:14px}
.intro p{font-size:13.5px;color:var(--muted);line-height:26px}
.btn-yellow{width:176px;height:52px;background:var(--yellow);display:flex;align-items:center;justify-content:center;font-size:17px;color:#333;font-weight:500}

.card{padding:60px 64px}
.card h3{font-size:31px;font-weight:600;line-height:48px;margin-bottom:14px;white-space:nowrap}
.card p{font-size:13.5px;line-height:26px}
.card-teal{background:var(--teal);color:var(--white)}
.card-yellow{background:var(--yellow);color:#2a2a2a}
.card-yellow h3{color:#222}

.promo{left:600px;top:1666px;width:279px;height:423px;background:var(--blue)}
.badge{left:940px;top:1975px;width:180px;height:70px;border-radius:8px;background:var(--badge)}

.brand{top:3640px;width:175px;text-align:center;font-size:22px;font-weight:600;color:#222;letter-spacing:1px;white-space:nowrap}
.frame{top:3740px;width:110px;height:50px;border-radius:24px}

.footer{left:0;top:3873px;width:1200px;height:403px;background:var(--footer-yellow)}
.fcol{top:3932px;width:330px}
.fcol h4{font-size:20px;color:var(--teal);font-weight:700;margin-bottom:26px}
.frow{display:flex;gap:16px;align-items:flex-start;font-size:14px;color:#333;line-height:22px;margin-bottom:19px}
.frow svg{flex:none;margin-top:3px}
.hours p{font-size:14px;color:#333;line-height:22px;margin-bottom:6px}
.hours b{font-weight:700}
.pill{top:4186px;width:279px;height:40px;border-radius:20px;background:var(--pill);color:var(--white);font-size:14px;display:flex;align-items:center;justify-content:space-between;padding:0 26px 0 18px}
.fsocial{top:4186px;width:40px;height:40px;border-radius:50%}
.copy{left:0;top:4276px;width:1200px;height:78px;background:var(--copy-yellow);display:flex;align-items:center;justify-content:center;font-size:13px;color:#777}
.copy b{color:var(--teal);font-weight:700}
</style>
</head>
<body>

<div class="abs topbar">
  <div class="abs item" style="left:463px">
    <svg width="18" height="18" viewBox="0 0 24 24" fill="none" stroke="#fde02a" stroke-width="2"><path d="M5 3h4l2 5-3 2a12 12 0 0 0 6 6l2-3 5 2v4a2 2 0 0 1-2 2A17 17 0 0 1 3 5a2 2 0 0 1 2-2z"/></svg>
    818-555-0142
  </div>
  <div class="abs item" style="left:635px">
    <svg width="20" height="16" viewBox="0 0 24 18" fill="none" stroke="#fde02a" stroke-width="2"><rect x="1" y="1" width="22" height="16"/><path d="M1 1l11 9 11-9"/></svg>
    info@lumoraoptometry.com
  </div>
  <div class="abs social" style="left:915px" role="img" aria-label="Social link"><span></span></div>
  <div class="abs social" style="left:967px" role="img" aria-label="Social link"><span></span></div>
  <div class="abs social" style="left:1019px" role="img" aria-label="Social link"><span></span></div>
  <div class="abs social" style="left:1071px" role="img" aria-label="Social link"><span></span></div>
</div>

<div class="abs logo">
  <div class="mark"></div>
  <div class="name">LUMORA<br>OPTOMETRY</div>
</div>
<nav class="abs nav">
  <span>Home</span><span>Our Team</span><span class="active">Eye Care</span><span>Myopia Control Clinic</span><span>Eyewear</span><span>Blog</span><span>Contact Us</span>
</nav>
<svg class="abs search" width="20" height="20" viewBox="0 0 24 24" fill="none" stroke="#0b8fae" stroke-width="2"><circle cx="10" cy="10" r="7"/><path d="M15 15l6 6"/></svg>

<div class="abs title-band"><h1>DRY EYE CLINIC</h1></div>

<div class="abs" style="left:78px;top:375px;width:503px;height:416px;background:linear-gradient(135deg,#7fc6e6 0%,#e8d6cc 45%,#b7998a 100%)" role="img" aria-label="Close-up of eye drops being applied to an open eye"></div>
<div class="abs about-text">
  <h2>ABOUT TEARS</h2>
  <p class="lead">The human eye is lubricated by two kinds of tears produced by glands in the upper and lower eyelid</p>
  <p>CONSTANT TEARS are continuously formed to lubricate the eye and contain natural antibiotics to help fight infections. When constant tears flow is reduced, there is irritation that can cause excessive reflex tearing "watery eyes. These excess tears lack the oil needed to keep from evaporating and do not lubricate the eye.</p>
  <p>REFLEX TEARS are produced only in response to irritation, injury or emotion. They help rinse the surface of the eye. A balance is necessary between the two types of tears to ensure that your eyes are comfortable and protected.</p>
</div>

<div class="abs intro" style="left:78px;top:866px">
  <h2>SYMPTOMS &amp; CAUSES</h2>
  <p>Symptoms of dry eyes can include redness, dryness, burning, grittiness, excessive tearing, tired eyes, blurry vision, and sensitivity to light. Patients with dry eyes can feel a debilitating...</p>
</div>
<div class="abs btn-yellow" style="left:78px;top:1014px">LEARN MORE</div>
<div class="abs intro" style="left:619px;top:866px">
  <h2>TREATMENT</h2>
  <p>Tears can be replaced by using eye drops , non preservative artificial tears. They replace the moisture that is missing and lubricate the eyes. Do not use preservative tears since that is the...</p>
</div>
<div class="abs btn-yellow" style="left:619px;top:1014px">LEARN MORE</div>

<div class="abs" style="left:78px;top:1142px;width:522px;height:523px;background:linear-gradient(135deg,#a9735a,#e9cdb9 55%,#f3ece6)" role="img" aria-label="Close-up portrait area of a woman's eye and cheek"></div>
<div class="abs card card-teal" style="left:537px;top:1215px;width:585px;height:375px">
  <h3>TEAR DUCT CLOSURE</h3>
  <p>Temporary closure of the tear duct (punctal canal) is accomplished by inserting a tiny PUNCTUM PLUG to prevent tear drainage. This allows your tears to bathe your eye for a longer period of time, reducing the burning irritating dry eye syndrome. Relief from the discomfort of dry eyes may take 1-2 weeks while some feel an immediate relief. Non preservative artificial tears may be used in conjunction with punctal plugs for maximum relief.</p>
</div>

<div class="abs promo" role="img" aria-label="Promotional graphic for the lid treatment"></div>
<div class="abs" style="left:879px;top:1666px;width:243px;height:274px;background:radial-gradient(circle at 55% 50%,#5a8fd0 0%,#9cc0e6 30%,#e6e0dc 65%,#c9b4a6 100%)" role="img" aria-label="Close-up of a blue eye"></div>
<div class="abs badge" role="img" aria-label="Treatment partner badge"></div>
<div class="abs card card-yellow" style="left:78px;top:1719px;width:584px;height:318px">
  <h3>LIDCLEAR</h3>
  <p>LidClear is a new, in-office procedure that allows a doctor to completely remove the scurf, debris, crusting, and exotoxin-laden biofilm that builds up on the patients lid margins over years. This biofilm causes the inflammation which slowly shuts down the tear glands and causes a wide range of other symptoms.</p>
</div>

<div class="abs" style="left:78px;top:2090px;width:522px;height:438px;background:linear-gradient(90deg,#8a6a4c,#e2cdb8 45%,#f7f5f2)" role="img" aria-label="Eyelid massage device held against a closed eye"></div>
<div class="abs card card-teal" style="left:537px;top:2163px;width:585px;height:282px">
  <h3>THE GLANDEASE SYSTEM IS</h3>
  <p>A natural way to significantly improve tear stability (and the amount of time it takes for your tears to evaporate) by increasing Meibomian gland output – this means your eyes stay lubricated and symptom-free longer, as nature intended.</p>
</div>

<div class="abs" style="left:600px;top:2528px;width:522px;height:522px;background:linear-gradient(135deg,#5a5a5a,#d9b7a5 45%,#eed8cb)" role="img" aria-label="Patient lying with eyes closed receiving a thermal eyelid treatment"></div>
<div class="abs card card-yellow" style="left:78px;top:2582px;width:584px;height:409px">
  <h3>THERMAGLOW THERMAL<br>TREATMENT</h3>
  <p>Great news! Dr. Mira Solen O.D., has done it again by introducing another "first!" As you know, Dr. Solen has been introducing the latest and greatest in eye care every year . We are proud to be one of the first eye care centers in California to introduce ThermaGlow thermoelectric technology for the treatment of dry eye. The revolutionary 10 minute per eye treatment relieves your dry eye symptoms. The treatment is painless, comfortable, and feels like a mini-spa on the eyes.</p>
</div>

<div class="abs" style="left:78px;top:3050px;width:522px;height:521px;background:linear-gradient(135deg,#f4f4f4,#d6d6d6 50%,#c79b86 80%,#eeeeee)" role="img" aria-label="Hand holding a handheld eyelid care device"></div>
<div class="abs card card-teal" style="left:537px;top:3123px;width:585px;height:385px">
  <h3 style="font-size:28px">GLANDEASE IS COMFORTABLE &amp;<br>EASY TO USE</h3>
  <p>"It's so fast, and that small little change in routine makes a huge difference in your overall lifestyle."</p>
  <p style="margin-top:26px">"At only 15 seconds per eyelid, it was so easy to add to my daily routine- brush my teeth, wash my face, and clean my eyelids. It's something I look forward to doing because I know how much of a difference it makes."</p>
</div>

<div class="abs brand" style="left:71px">VANTO</div>
<div class="abs brand" style="left:248px">ORLEN MARSH</div>
<div class="abs brand" style="left:425px">BELLCOURT</div>
<div class="abs brand" style="left:602px">VELOCE</div>
<div class="abs brand" style="left:779px">MAISON RIVE</div>
<div class="abs brand" style="left:956px">DRAKEN</div>
<div class="abs frame" style="left:104px;background:linear-gradient(90deg,#1f3550,#5a7fa8)" role="img" aria-label="Sunglasses"></div>
<div class="abs frame" style="left:281px;background:linear-gradient(90deg,#4a2a1c,#8a5a3c)" role="img" aria-label="Tortoiseshell eyeglasses"></div>
<div class="abs frame" style="left:458px;background:linear-gradient(90deg,#8a5a44,#d9b49c)" role="img" aria-label="Brown tinted sunglasses"></div>
<div class="abs frame" style="left:635px;background:linear-gradient(90deg,#e8d8c4,#f7efe6)" role="img" aria-label="Light gold eyeglasses"></div>
<div class="abs frame" style="left:812px;background:linear-gradient(90deg,#1a1a1a,#4a4a4a)" role="img" aria-label="Black eyeglasses"></div>
<div class="abs frame" style="left:989px;background:linear-gradient(90deg,#d8c9b6,#f1e8dd)" role="img" aria-label="Cream sunglasses"></div>

<div class="abs footer"></div>
<div class="abs fcol" style="left:78px">
  <h4>Lumora Optometry</h4>
  <div class="frow"><svg width="20" height="20" viewBox="0 0 24 24" fill="#0b8fae"><path d="M5 2h4l2 6-3 2a12 12 0 0 0 6 6l2-3 6 2v4a3 3 0 0 1-3 3A18 18 0 0 1 2 5a3 3 0 0 1 3-3z"/></svg>818-555-0142</div>
  <div class="frow"><svg width="22" height="20" viewBox="0 0 24 22" fill="#0b8fae"><rect x="5" y="1" width="14" height="6"/><rect x="1" y="8" width="22" height="10" rx="2"/><rect x="5" y="14" width="14" height="7" fill="#fff" stroke="#0b8fae" stroke-width="2"/></svg>818-555-0178</div>
  <div class="frow"><svg width="20" height="16" viewBox="0 0 24 18" fill="#0b8fae"><rect width="24" height="18"/><path d="M0 0l12 9 12-9" stroke="#fbe45c" stroke-width="2" fill="none"/></svg>info@brivaloka.com</div>
  <div class="frow"><svg width="16" height="22" viewBox="0 0 16 22" fill="#0b8fae"><path d="M8 0a8 8 0 0 1 8 8c0 6-8 14-8 14S0 14 0 8a8 8 0 0 1 8-8z"/><circle cx="8" cy="8" r="3" fill="#fbe45c"/></svg>4821 Calder Ave., Westmere,<br>CA 91402</div>
</div>
<div class="abs fcol" style="left:435px">
  <h4>Northgate</h4>
  <div class="frow"><svg width="20" height="20" viewBox="0 0 24 24" fill="#0b8fae"><path d="M5 2h4l2 6-3 2a12 12 0 0 0 6 6l2-3 6 2v4a3 3 0 0 1-3 3A18 18 0 0 1 2 5a3 3 0 0 1 3-3z"/></svg>818-555-0196</div>
  <div class="frow"><svg width="20" height="16" viewBox="0 0 24 18" fill="#0b8fae"><rect width="24" height="18"/><path d="M0 0l12 9 12-9" stroke="#fbe45c" stroke-width="2" fill="none"/></svg>northgate@brivaloka.com</div>
  <div class="frow"><svg width="16" height="22" viewBox="0 0 16 22" fill="#0b8fae"><path d="M8 0a8 8 0 0 1 8 8c0 6-8 14-8 14S0 14 0 8a8 8 0 0 1 8-8z"/><circle cx="8" cy="8" r="3" fill="#fbe45c"/></svg>2290 Harlow St., Suite 4,<br>Northgate, CA 91408</div>
</div>
<div class="abs fcol hours" style="left:792px">
  <h4>Opening Hours</h4>
  <p>Monday - Thursday : <b>9 am - 6 pm</b></p>
  <p>Friday : <b>8.30 am - 5 pm</b></p>
  <p>Saturday &nbsp;: <b>8.30 am- 5 pm</b></p>
  <p>Closed on <b>Sundays</b></p>
  <p>Please keep in mind we are closed<br>for <b>lunch 1-2 pm</b></p>
</div>
<div class="abs pill" style="left:78px">Get directions on the map
  <svg width="30" height="8" viewBox="0 0 30 8" fill="none" stroke="#0b8fae" stroke-width="1.5"><path d="M0 4h28M24 1l4 3-4 3"/></svg></div>
<div class="abs pill" style="left:435px">Get directions on the map
  <svg width="30" height="8" viewBox="0 0 30 8" fill="none" stroke="#0b8fae" stroke-width="1.5"><path d="M0 4h28M24 1l4 3-4 3"/></svg></div>
<div class="abs fsocial" style="left:792px;background:var(--teal)" role="img" aria-label="Social link"></div>
<div class="abs fsocial" style="left:842px;background:var(--pill)" role="img" aria-label="Social link"></div>
<div class="abs fsocial" style="left:892px;background:var(--pill)" role="img" aria-label="Social link"></div>
<div class="abs fsocial" style="left:942px;background:var(--pill)" role="img" aria-label="Social link"></div>

<div class="abs copy"><span>Copyright ©&nbsp;<b>LUMORA OPTOMETRY</b>&nbsp;- 2019 . All right Resereved</span></div>

</body>
</html>
```